We need a logo design that explain all the products we possess.
The main goal is to represent graphically all the logos, pointing to one single logo - Vellamor.
The descriptions are in french.
I have uploaded a file with 4 logos to use:
Vellamor (the logo that all the rest should be pointing to)
RTN
Ombrevik
TroupéLune
All logo must be used in the vector graphic format, the description file is in each folder, it's the description that should be next to the logo.

The main goal of this is to create a banner 10' x 11' (estimated)

Target Market(s)

Cities

Requirements
Must have
• All the logos in the zip file in vector graphic.
Nice to have
• A background
Should not have
• Do not use KOL logo, it's a mix with RTN, and Kol Blue/dark blue with inscription "RTN", Charging fees for a part of the picture is not ok!

```html
<!DOCTYPE html>
<html lang="fr">
<head>
<meta charset="utf-8">
<title>Portail Vellamor 2.0 – Bannière</title>
<link rel="stylesheet" href="https://fonts.googleapis.com/css2?family=Roboto:wght@700;900&display=swap">
<style>
  :root {
    --page: #ececec;
    --sky-top: #2a6cc4;
    --sky-mid: #6f9fd8;
    --sky-low: #c8dbef;
    --city-top: #b9c3cc;
    --city-mid: #8c8a86;
    --city-low: #5a5650;
    --ink: #111111;
    --ring-dark: #222222;
    --ring-grey: #e4e4e7;
    --white: #ffffff;
    --green: #7dc242;
    --teal: #5aaab0;
    --blue: #23a0e8;
    --brand-blue: #1e6fb8;
    --base-bar: #9acd3c;
  }
  * { margin: 0; padding: 0; box-sizing: border-box; }
  html, body {
    width: 1200px;
    height: 1200px;
    overflow: hidden;
    background: var(--page);
  }
  .banner {
    position: absolute;
    left: 0;
    top: 132px;
    width: 1200px;
    height: 936px;
    overflow: hidden;
  }
  .banner__sky {
    position: absolute;
    inset: 0;
    background: linear-gradient(180deg, var(--sky-top) 0%, var(--sky-mid) 35%, var(--sky-low) 75%, #dfe8f1 100%);
  }
  .banner__skyline {
    position: absolute;
    left: 0;
    right: 0;
    top: 620px;
    bottom: 9px;
    background: linear-gradient(180deg, rgba(185,195,204,0) 0%, var(--city-top) 30%, var(--city-mid) 70%, var(--city-low) 100%);
  }
  .banner__base {
    position: absolute;
    left: 0;
    right: 0;
    bottom: 0;
    height: 9px;
    background: var(--base-bar);
  }
  .diagram {
    position: absolute;
    inset: 0;
    width: 1200px;
    height: 936px;
  }
  .label {
    font-family: "Roboto", Arial, sans-serif;
    font-weight: 900;
    font-size: 25px;
    fill: var(--ink);
    text-anchor: middle;
  }
  .brand-name {
    font-family: "Roboto", Arial, sans-serif;
    font-weight: 900;
    text-anchor: middle;
  }
  .brand-name--main { font-size: 46px; fill: var(--brand-blue); }
  .brand-name--green { font-size: 34px; fill: var(--brand-blue); }
  .brand-name--teal { font-size: 24px; fill: var(--brand-blue); }
  .brand-name--blue { font-size: 22px; fill: var(--blue); }
</style>
</head>
<body>
  <main class="banner">
    <div class="banner__sky" role="img" aria-label="Photo de ciel bleu nuageux au-dessus de la ville"></div>
    <div class="banner__skyline" role="img" aria-label="Photo de la ligne d'horizon d'une ville avec gratte-ciel"></div>
    <div class="banner__base"></div>

    <svg class="diagram" viewBox="0 0 1200 936" aria-label="Produits reliés au portail Vellamor">
      <defs>
        <filter id="soft-shadow" x="-30%" y="-30%" width="160%" height="160%">
          <feDropShadow dx="0" dy="8" stdDeviation="9" flood-color="#000" flood-opacity="0.25"/>
        </filter>
      </defs>

      <!-- hub -->
      <g class="hub">
        <circle cx="602" cy="274" r="217" fill="var(--white)"/>
        <path d="M385 274 A217 217 0 0 1 819 274" fill="none" stroke="var(--ring-dark)" stroke-width="3"/>
        <path d="M385 274 A217 217 0 0 0 403 361" fill="none" stroke="var(--ring-dark)" stroke-width="4" stroke-dasharray="10 5"/>
        <path d="M403 361 A217 217 0 0 0 530 479" fill="none" stroke="var(--green)" stroke-width="4" stroke-dasharray="10 5"/>
        <path d="M530 479 A217 217 0 0 0 674 479" fill="none" stroke="var(--teal)" stroke-width="4" stroke-dasharray="10 5"/>
        <path d="M674 479 A217 217 0 0 0 801 361" fill="none" stroke="var(--blue)" stroke-width="4" stroke-dasharray="10 5"/>
        <path d="M801 361 A217 217 0 0 0 819 274" fill="none" stroke="var(--ring-dark)" stroke-width="4" stroke-dasharray="10 5"/>
        <circle cx="385" cy="274" r="8" fill="var(--white)" stroke="var(--ring-dark)" stroke-width="4"/>
        <circle cx="819" cy="274" r="8" fill="var(--white)" stroke="var(--ring-dark)" stroke-width="4"/>
        <circle cx="602" cy="274" r="194" fill="var(--ring-grey)"/>
        <circle cx="602" cy="274" r="164" fill="var(--white)" filter="url(#soft-shadow)"/>
        <text class="brand-name brand-name--main" x="602" y="255">VELLAMOR</text>
        <text class="label" x="602" y="342">PORTAIL</text>
        <text class="label" x="602" y="374">VELLAMOR 2.0</text>
      </g>

      <!-- arrows -->
      <polygon points="375,390 428,372 418,424 408,404 392,412" fill="var(--green)"/>
      <polygon points="572,485 602,460 632,485 616,485 616,495 588,495 588,485" fill="var(--teal)"/>
      <polygon points="829,390 776,372 786,424 796,404 812,412" fill="var(--blue)"/>

      <!-- RTN -->
      <g class="product product--rtn">
        <circle cx="330" cy="464" r="80" fill="var(--white)" stroke="var(--green)" stroke-width="11"/>
        <text class="brand-name brand-name--green" x="330" y="477">RTN</text>
        <text class="label" x="321" y="582">CONSEIL</text>
        <text class="label" x="321" y="614">SANS PAPIER</text>
      </g>

      <!-- Ombrevik -->
      <g class="product product--ombrevik">
        <circle cx="602" cy="571" r="80" fill="var(--white)" stroke="var(--teal)" stroke-width="11"/>
        <text class="brand-name brand-name--teal" x="602" y="580">OMBREVIK</text>
        <text class="label" x="602" y="685">PERMIS | CARTE</text>
        <text class="label" x="602" y="717">INVENTAIRE | TAXES</text>
      </g>

      <!-- TroupéLune -->
      <g class="product product--troupelune">
        <circle cx="873" cy="464" r="80" fill="var(--white)" stroke="var(--blue)" stroke-width="11"/>
        <text class="brand-name brand-name--blue" x="873" y="472">TroupéLune</text>
        <text class="label" x="875" y="582">LICENCES</text>
        <text class="label" x="875" y="614">POUR ANIMAUX</text>
      </g>
    </svg>
  </main>
</body>
</html>
```